Coastal Learner Bureau business cards

Australian company about to start offering its services. We recruit international students to come to study English, vocational education and postgraduate courses in Australia. We help them find the institution and select the right city they want to come to Australia. We are a young, online oriented and supportive agency. Our clients are between 18 and 35 years old, mainly University students, young professionals or people with work experience. We provide much more information that any other agency offer. We administrate a Facebook group with more than 11.000 members that daily ask questions about general information when coming to Australia, while they are here and even after they leave the country

Target Market(s)

International students from South America, Central America and Europe

Industry/Entity Type

Student

Contact Information for Business Card

Tomas Bilbrea
Managing Director
tomas@kelvarin.com.au
www.kelvoria.com.au
+61 491058264
Melbourne, Australia

Font styles to use
Serif
Sans Serif

Colors

Designer to choose colors to be used in the design.

Requirements
Must have
• Horizontal design
• Standard business card size and shape. If font uses green or yellow colours, they will have to match the ones from the logo
Nice to have
• UPDATE: Use the contents of the green image to design one of the card sides. Use our logo in the background of that side as watermark.
• Passport image, or immigration stamps. A picture of the Yarra River (from Melbourne) would be cool as well.
Should not have
• Non-standard business card size and shape
• Not black as the background colour of any sides as we are not a VIP agency or a hight class service. We are orientes to young people and they like colours, pictures, something attractive.
• Vertical design
• NO YELLOW or BLACK AS THE BACKGROUND COLOUR OF ANY SIDE OF THE BIZ CARD

```html
<!DOCTYPE html>
<html lang="en">
<head>
<meta charset="utf-8">
<title>Coastal Learner Bureau business cards</title>
<link rel="stylesheet" href="https://fonts.googleapis.com/css2?family=Oswald:wght@400;500&display=swap">
<style>
  :root{
    --backdrop:#0c0c0c;
    --brand-green:#17613f;
    --deep-green:#0f4a30;
    --brand-yellow:#e3b925;
    --paper:#faf7f1;
    --ink-light:#ffffff;
  }
  *{box-sizing:border-box;margin:0;padding:0}
  html,body{width:1200px;height:1000px;overflow:hidden;background:var(--backdrop)}
  .stage{position:relative;width:1200px;height:1000px;font-family:"Oswald",sans-serif}
  .card{position:absolute;top:357px;width:500px;height:286px;box-shadow:0 6px 18px rgba(0,0,0,.55)}
  .card-back{left:75px;background:var(--brand-green);display:flex;align-items:center;justify-content:center}
  .watermark-name{font-size:78px;font-weight:500;color:#14583a;letter-spacing:1px}
  .card-front{left:625px;background:var(--paper)}
  .identity{position:absolute;left:30px;top:92px}
  .brand-name{display:flex;align-items:center;gap:10px;font-size:34px;font-weight:500;color:var(--brand-green)}
  .brand-dot{width:14px;height:14px;border-radius:50%;background:var(--brand-yellow)}
  .person-name{margin-top:14px;font-size:27px;font-weight:500;letter-spacing:.5px}
  .person-first{color:var(--brand-green)}
  .person-last{color:var(--brand-yellow)}
  .city-photo{position:absolute;left:276px;top:22px;width:202px;height:246px;
    background:linear-gradient(180deg,#1f6a4a 0%,#14573b 45%,#0e4530 100%)}
  .icon-rail{position:absolute;left:262px;top:40px;width:34px;height:196px;border-radius:17px;
    background:var(--brand-yellow);display:flex;flex-direction:column;justify-content:space-around;align-items:center;padding:8px 0}
  .icon-rail svg{width:18px;height:18px;fill:var(--deep-green)}
  .contact-list{position:absolute;left:308px;top:42px;list-style:none;color:var(--ink-light);
    font-size:13px;letter-spacing:.4px;line-height:1}
  .contact-list li{height:38.5px;display:flex;align-items:center}
  .contact-role{font-weight:500;font-size:14px}
</style>
</head>
<body>
<main class="stage">
  <section class="card card-back" aria-label="Card back">
    <span class="watermark-name">Kelvoria</span>
  </section>

  <section class="card card-front" aria-label="Card front">
    <div class="identity">
      <div class="brand-name"><span class="brand-dot"></span>Kelvoria</div>
      <div class="person-name"><span class="person-first">TOMAS</span> <span class="person-last">BILBREA</span></div>
    </div>

    <div class="city-photo" role="img" aria-label="Green-toned photo of the Melbourne skyline over the Yarra River"></div>

    <div class="icon-rail">
      <svg viewBox="0 0 24 24" aria-label="Person"><circle cx="12" cy="7" r="5"/><path d="M2 23c0-6 4.5-9 10-9s10 3 10 9z"/></svg>
      <svg viewBox="0 0 24 24" aria-label="Phone"><path d="M6.6 2.5l3 4.2-2 2.3c1.3 2.7 3.6 5 6.3 6.3l2.3-2 4.2 3-1.7 4.2C10.8 21 3 13.2 2.5 4.2z"/></svg>
      <svg viewBox="0 0 24 24" aria-label="Email"><path d="M2 5h20v14H2z M3.5 6.5 12 13l8.5-6.5" stroke="#e3b925" stroke-width="1.6"/></svg>
      <svg viewBox="0 0 24 24" aria-label="Website"><path d="M12 2a10 10 0 1 0 0 20 10 10 0 0 0 0-20zm0 2c1.6 1.8 2.4 4.8 2.5 7h-5c.1-2.2.9-5.2 2.5-7zM4.1 11a8 8 0 0 1 3.9-6.1c-.9 1.8-1.4 4-1.5 6.1zm0 2h2.4c.1 2.1.6 4.3 1.5 6.1A8 8 0 0 1 4.1 13zm5.4 0h5c-.1 2.2-.9 5.2-2.5 7-1.6-1.8-2.4-4.8-2.5-7zm8 0h2.4a8 8 0 0 1-3.9 6.1c.9-1.8 1.4-4 1.5-6.1zm0-2c-.1-2.1-.6-4.3-1.5-6.1a8 8 0 0 1 3.9 6.1z"/></svg>
      <svg viewBox="0 0 24 24" aria-label="Location"><path d="M12 1a8 8 0 0 0-8 8c0 6 8 14 8 14s8-8 8-14a8 8 0 0 0-8-8zm0 11a3 3 0 1 1 0-6 3 3 0 0 1 0 6z"/></svg>
    </div>

    <ul class="contact-list">
      <li class="contact-role">MANAGING DIRECTOR</li>
      <li>+61 49 10 58 264</li>
      <li>TOMAS@KELVARIN.COM.AU</li>
      <li>WWW.KELVORIA.COM.AU</li>
      <li>MELBOURNE, AUSTRALIA</li>
    </ul>
  </section>
</main>
</body>
</html>
```